Visitenkarten für Mentorin für Frauen
Zielgruppe
Ich bin Mentorin für Frauen (30-50 Jahre alt), die ihre Berufung endlich finden möchten und sich nach mehr Energie und Sinn sehnen. Ich helfe ihnen mit meiner (Name fehtl noch)-Methode ihren Seelenweg zu finden und zu gehen, sodass sie vor Energie übersprudeln und mit einem Leuchten in den Augen ein Leben in Fluss und Fülle kreieren.
Sie sind nicht unglücklich, aber es fehtl ihnen was, das sie wirklich erfüllt.
Stichwörter: Numerologie, Human Design, Seelenweg, Berufung, Lebensaufgabe, erfüllt sein- endlich die Leere füllen, Freiheit, Selbstbestimmt, Selbstliebe, Potentialentfaltung, Transformation
meine core story:
Mit Freude, unglaublicher Energie und einem Strahlen in den Augen schon vor dem Wecker aufzustehen, war für mich früher undenkbar. Ich konnte mir nicht vorstellen, wie sich Leute auf den Montag freuen konnten.
Dabei hätte mich nicht als unglücklich bezeichnet, aber es fehlt einfach etwas, ich hatte eine innere Leere und eine Sehnsucht nach dem Sinn in meinem Lebe, wollte so geliebt werden wie ich bin und mich auch so zeigen können. Ich weiß wie es ist sich klein, unsicher zu fühlen und nicht zu wissen woher das kommt. Ich habe es einfach nicht für möglich gehalten, dass diese innere Leere so leicht zu füllen ist und Freude, Spaß, Selbstbewusstseein und Leichtigkeit in allen Bereichen mit sich bringt.
Weil ich selbst diesen Weg gegangen bin und weil ich weiß, dass es nichts erfüllenderes gibt als das schlummernde Potential zu erwecken, begleite ich Frauen dabei ihren Seelenweg zu finden und zu gehen.
Dadurch dass sie genau wissen, was ihre Gaben sind und was ihre Seele glücklich macht, haben sie Spaß und Freude, gerade auch in den alltäglichen Dingen. Sie führen ein selbstbestimmtes Leben, lieben sich selbst und zeigen sich so wie sie sind.Die gigantische Energie die dadurch in ihnen frei wird, lässt sie die bisherigen Grenzen überwinden. Sie tun was sie erfüllt, o..
Aufgabenstellung
weiblich, geschwungen, weich: beinhalten solls:
Marlene Wittberg
Mentorin für Powerfrauen
(Lebe deine Berufung)--> da bin ich mir nicht ganz sicher ob das gut aussehn wird oder zuviel wird
falls relevant habe ich bisher folgende Schriftarten verwendet: Canva Sans und Tan mon cheri
ist aber kein muss

```html
<!DOCTYPE html>
<html lang="de">
<head>
<meta charset="utf-8">
<title>Visitenkarte – Marlene Wittberg</title>
<link rel="stylesheet" href="https://fonts.googleapis.com/css2?family=Bodoni+Moda:wght@400;500&family=Montserrat:wght@400;500&display=swap">
<style>
  :root {
    --card: #f6f4ef;
    --bronze: #a27b4c;
    --bronze-soft: #b8956a;
    --art-light: #efe6d8;
    --art-mid: #dcc7a6;
  }
  * { margin: 0; padding: 0; box-sizing: border-box; }
  html, body {
    width: 1200px;
    height: 801px;
    overflow: hidden;
    background: var(--card);
  }
  .card {
    position: relative;
    width: 1200px;
    height: 801px;
    background: var(--card);
    color: var(--bronze);
  }
  .card__art {
    position: absolute;
    left: 60px;
    top: 40px;
    width: 350px;
    height: 690px;
    border-radius: 170px 170px 40px 40px;
    background: radial-gradient(ellipse at 50% 35%, var(--art-mid) 0%, var(--art-light) 55%, var(--card) 100%);
  }
  .card__divider {
    position: absolute;
    left: 497px;
    top: 145px;
    height: 575px;
    border-left: 3px dotted var(--bronze-soft);
  }
  .card__info {
    position: absolute;
    left: 580px;
    top: 78px;
  }
  .card__name {
    font-family: "Bodoni Moda", serif;
    font-weight: 500;
    font-size: 72px;
    line-height: 96px;
    letter-spacing: -0.01em;
    text-transform: uppercase;
  }
  .card__title {
    margin-top: 14px;
    font-family: "Montserrat", sans-serif;
    font-weight: 500;
    font-size: 34px;
    line-height: 58px;
    letter-spacing: 0.3em;
    text-transform: uppercase;
  }
  .contact {
    list-style: none;
    margin-top: 58px;
  }
  .contact__item {
    display: flex;
    align-items: center;
    height: 85px;
    font-family: "Montserrat", sans-serif;
    font-size: 32px;
  }
  .contact__icon {
    width: 40px;
    height: 40px;
    margin-right: 44px;
    fill: var(--bronze);
  }
  .contact__icon--line {
    fill: none;
    stroke: var(--bronze);
    stroke-width: 1.6;
  }
</style>
</head>
<body>
  <main class="card">
    <div class="card__art" role="img" aria-label="Linienzeichnung einer sitzenden Frau von hinten mit geflochtenem Blumenhaar und Schmetterlingen"></div>
    <div class="card__divider"></div>

    <section class="card__info">
      <h1 class="card__name">Marlene<br>Wittberg</h1>
      <p class="card__title">Mentorin für<br>Powerfrauen</p>

      <ul class="contact">
        <li class="contact__item">
          <svg class="contact__icon" viewBox="0 0 24 24" aria-hidden="true">
            <path d="M6.6 10.8c1.4 2.8 3.8 5.1 6.6 6.6l2.2-2.2c.3-.3.7-.4 1-.2 1.1.4 2.3.6 3.6.6.6 0 1 .4 1 1V20c0 .6-.4 1-1 1C10.6 21 3 13.4 3 4c0-.6.4-1 1-1h3.5c.6 0 1 .4 1 1 0 1.3.2 2.5.6 3.6.1.3 0 .7-.2 1z"/>
          </svg>
          <span>telefon</span>
        </li>
        <li class="contact__item">
          <svg class="contact__icon" viewBox="0 0 24 24" aria-hidden="true">
            <path d="M12 2 2 8.5V20c0 .6.4 1 1 1h18c.6 0 1-.4 1-1V8.5L12 2zm0 11.2L4.6 8.6 12 4l7.4 4.6L12 13.2z"/>
          </svg>
          <span>email</span>
        </li>
        <li class="contact__item">
          <svg class="contact__icon" viewBox="0 0 24 24" aria-hidden="true">
            <path d="M12 2C8.1 2 5 5.1 5 9c0 5.2 7 13 7 13s7-7.8 7-13c0-3.9-3.1-7-7-7zm0 9.5a2.5 2.5 0 1 1 0-5 2.5 2.5 0 0 1 0 5z"/>
          </svg>
          <span>adresse</span>
        </li>
        <li class="contact__item">
          <svg class="contact__icon contact__icon--line" viewBox="0 0 24 24" aria-hidden="true">
            <circle cx="12" cy="12" r="9"/>
            <ellipse cx="12" cy="12" rx="4" ry="9"/>
            <path d="M3 12h18M4.5 7.5h15M4.5 16.5h15"/>
          </svg>
          <span>webseite</span>
        </li>
      </ul>
    </section>
  </main>
</body>
</html>
```